Kelvor Guard Installations - Alarm and CCTV installation Flyer

Need a flyer designed that grabs the attention of potential customers, we need the price to stand out the most to grab people’s attention, whether they are residential or commercial.We are a security company based in Brentwood Essex but cover London and the home counties. here is our website to take a look at www.kelvorguardinstalls.co.uk. We want them to know we install complete alarm and Cctv systems and will keep them “safe”

Target Market(s)

residential and commercial property

Colors
f37122

Requirements
Must have
• on one side
• large clear logo - professional design
• - Intruder Alarms starting from £495 + VAT. (Big text)
• - £150 discount on installations
• *terms and conditions apply (small text)
• - Not happy with your current provider? Free of charge no obligation take over survey and quotation and up to £100 off
• - CCTV systems starting from £595 + VAT (based on 2 cameras)
• Kelvor Guard Installations are always there, always available, wherever and whenever you need us.
• Large telephone number at the bottom 01632 908417
• Address / email / website as a footer * see website for details
• on second side
• large and bold
• Are you looking to keep you and your premises safe?
• - Kelvor Guard Installations install, maintain and repair all intruder alarms, CCTV, intercom and access control
• - View, control and manage your security systems anywhere in the world
• - Feel at ease with monitoring services & police response tailored to suit you and your business
• - Kelvor Guard can takeover any existing security system and offer maintenance checks to guarantee the best performance for you and your premises
• - Kelvor Guard understand that being security conscious is ever increasing, protecting your property and family is a number one priority
• - Our fully insured and accredited team offer quality, safety and cost efficiency throughout the whole process
• - Kelvor Guard Installations are using the latest cloud-based technology to stay connected with your home and business 24/7
• If you are looking to improve the security in your home, office or commercial property then call a member of our team today for a free quote.
• Fully insured and accredited
• Tradevouch logo and NQPRB Intruder and CCTV logos
• Logo somewhere on page and
• Telephone number
• Address / email / website as footer
Nice to have
• We would like to have the text saying
• Intruder alarms installed from £495 + vat the biggest text on the page. Most likely the £495 part the largest.
• Also would like “not happy with your current provider” more obvious
• We would like use our company colours - Orange/White/black

```html
<!DOCTYPE html>
<html lang="en">
<head>
<meta charset="utf-8">
<title>Kelvor Guard Installations – Alarm and CCTV Flyer</title>
<link href="https://fonts.googleapis.com/css2?family=Oswald:wght@400;500;600&family=Open+Sans:wght@400;600;700&display=swap" rel="stylesheet">
<style>
  :root{
    --orange:#f37122;
    --orange-deep:#e8561c;
    --ink:#3a3a3c;
    --charcoal:#3d3d40;
    --panel:#e9e9eb;
    --white:#ffffff;
    --page:#d9d6d2;
    --muted:#5a5a5e;
  }
  *{box-sizing:border-box;margin:0;padding:0}
  html,body{width:1200px;height:790px;overflow:hidden}
  body{background:var(--page);font-family:"Open Sans",Arial,sans-serif;color:var(--ink);position:relative}
  .flyer{position:absolute;top:60px;width:470px;height:670px;background:var(--white);overflow:hidden;box-shadow:0 4px 14px rgba(0,0,0,.25)}
  .flyer--offer{left:90px}
  .flyer--info{left:640px}

  /* imagery blocks */
  .photo{position:absolute}
  .flyer--offer .photo--hero{left:0;top:0;width:470px;height:305px;
    background:linear-gradient(115deg,#d7d9dc 0%,#eceef0 35%,#bfc2c6 55%,#f2f2f2 75%,#9ea3a8 100%)}
  .flyer--offer .photo--phones{left:275px;top:170px;width:150px;height:160px;border-radius:12px;
    background:linear-gradient(160deg,#2b2f38 0%,#3aa6e0 45%,#f0f4f7 100%)}
  .hero-band{position:absolute;left:0;top:260px;width:470px;height:60px}
  .flyer--info .photo--hero{left:0;top:0;width:470px;height:262px;
    background:linear-gradient(110deg,#c9ced3 0%,#e6e9ec 40%,#b7bcc0 65%,#8d8378 100%)}

  /* logo */
  .logo-plate{position:absolute;top:0;width:215px;height:95px}
  .flyer--offer .logo-plate{left:0}
  .flyer--info .logo-plate{right:0}
  .logo{position:absolute;top:12px;width:190px;text-align:center;color:var(--orange);font-family:"Open Sans",Arial,sans-serif;font-weight:600;line-height:1.05}
  .flyer--offer .logo{left:6px}
  .flyer--info .logo{right:6px}
  .logo__mark{display:block;width:34px;height:34px;margin:0 auto 5px;border-radius:50%;background:var(--orange)}
  .logo__name{display:block;font-size:20px;letter-spacing:.5px}
  .logo__sub{display:block;font-size:11px;letter-spacing:2px;margin-top:2px}

  /* offer side */
  .switch-heading{position:absolute;left:25px;top:336px;font-family:"Oswald",Arial,sans-serif;font-weight:500;font-size:21px;line-height:1.22;color:var(--ink);text-transform:uppercase}
  .switch-offer{position:absolute;left:25px;top:407px;font-size:10.6px;font-weight:600;color:var(--orange)}
  .price-panel{position:absolute;left:0;top:436px;width:470px;height:152px;background:var(--panel);display:flex}
  .price{flex:1;text-align:center;padding-top:14px;position:relative}
  .price + .price::before{content:"";position:absolute;left:0;top:16px;bottom:16px;border-left:1px dotted #a8a8ac}
  .price__icon{display:block;margin:0 auto 8px;height:44px}
  .price__label{font-size:11px;line-height:1.25;color:var(--muted)}
  .price__big{font-family:"Oswald",Arial,sans-serif;font-weight:500;color:var(--orange);font-size:22px;line-height:1.1}
  .price__note{font-size:8.5px;color:var(--muted);line-height:1.2}
  .always{position:absolute;left:0;width:470px;top:603px;text-align:center;font-size:9.6px;color:var(--orange-deep)}

  /* info side */
  .safe-banner{position:absolute;left:0;top:264px;width:470px;height:52px;background:var(--orange-deep);line-height:52px;text-align:center;white-space:nowrap;font-family:"Oswald",Arial,sans-serif;font-weight:500;font-size:18px;color:var(--white);text-transform:uppercase;letter-spacing:0}
  .safe-banner__word{display:inline-block;line-height:26px;background:var(--charcoal);padding:0 4px}
  .benefits{position:absolute;left:10px;top:326px;width:450px;height:218px;background:var(--panel);list-style:none;padding:10px 14px 0 12px}
  .benefits li{display:flex;gap:7px;font-size:8.6px;line-height:1.3;color:var(--ink);margin-bottom:9.5px}
  .benefits svg{flex:none;margin-top:1px}
  .trust{position:absolute;left:0;width:470px;top:553px;display:flex;align-items:center;justify-content:center;gap:14px}
  .trust__name{font-size:14px;font-weight:700;color:var(--orange-deep);margin-right:12px}
  .badge{width:24px;height:24px;border-radius:50%;border:1.5px solid #7c8088;background:var(--white)}
  .badge--square{border-radius:3px;width:22px;height:26px}
  .closing{position:absolute;left:0;width:470px;top:590px;text-align:center;font-size:9.6px;line-height:1.35;color:var(--orange-deep)}

  /* footer */
  .footer{position:absolute;left:0;bottom:0;width:470px;height:42px}
  .footer svg.footer__bg{position:absolute;left:0;top:0}
  .footer__phone{position:absolute;left:14px;top:10px;display:flex;align-items:center;gap:6px;color:var(--white);font-weight:600;font-size:16px;letter-spacing:.3px}
  .footer__contact{position:absolute;right:10px;top:8px;text-align:right;color:var(--white);line-height:1.45}
  .footer__web{font-size:8.2px;font-weight:600}
  .footer__address{font-size:7.4px}
</style>
</head>
<body>

<!-- Side one: offers -->
<section class="flyer flyer--offer">
  <div class="photo photo--hero" role="img" aria-label="Photograph of a security alarm keypad, a wall-mounted CCTV camera and a spiral staircase"></div>
  <div class="photo photo--phones" role="img" aria-label="Photograph of two smartphones showing the alarm control app"></div>
  <svg class="hero-band" viewBox="0 0 470 60" aria-hidden="true">
    <polygon points="0,30 275,50 275,60 0,60" fill="var(--white)"/>
    <polygon points="0,22 250,44 275,50 0,30" fill="var(--orange-deep)"/>
    <polygon points="275,50 470,30 470,60 275,60" fill="var(--white)"/>
  </svg>

  <svg class="logo-plate" viewBox="0 0 215 95" aria-hidden="true">
    <polygon points="0,0 215,0 188,95 0,95" fill="var(--white)"/>
    <polygon points="200,0 215,0 190,95 176,95" fill="#cfd1d4"/>
  </svg>
  <div class="logo">
    <span class="logo__mark"></span>
    <span class="logo__name">KELVOR GUARD</span>
    <span class="logo__sub">INSTALLATIONS</span>
  </div>

  <h2 class="switch-heading">Not happy with<br>your current provider?</h2>
  <p class="switch-offer">Free of charge no obligation take over survey and quotation and up to £100 off</p>

  <div class="price-panel">
    <div class="price">
      <svg class="price__icon" width="44" height="44" viewBox="0 0 44 44" aria-hidden="true">
        <rect x="15" y="8" width="14" height="26" rx="3" fill="var(--orange-deep)"/>
        <circle cx="22" cy="16" r="3" fill="var(--white)"/>
        <path d="M9 12 Q5 21 9 30 M4 9 Q-1 21 4 33 M35 12 Q39 21 35 30 M40 9 Q45 21 40 33" stroke="var(--orange-deep)" stroke-width="2.2" fill="none"/>
      </svg>
      <p class="price__label">Intruder Alarms<br>starting from</p>
      <p class="price__big">£495 + VAT</p>
    </div>
    <div class="price">
      <svg class="price__icon" width="44" height="44" viewBox="0 0 44 44" aria-hidden="true">
        <g fill="var(--orange-deep)">
          <circle cx="18" cy="26" r="11"/>
          <circle cx="32" cy="12" r="7"/>
        </g>
        <g stroke="var(--orange-deep)" stroke-width="4" stroke-linecap="square">
          <path d="M18 11v30M3 26h30M7 15l22 22M29 15L7 37"/>
          <path d="M32 2v20M22 12h20M25 5l14 14M39 5L25 19" stroke-width="3"/>
        </g>
        <circle cx="18" cy="26" r="4.5" fill="var(--panel)"/>
        <circle cx="32" cy="12" r="3" fill="var(--panel)"/>
      </svg>
      <p class="price__big">£150 DISCOUNT</p>
      <p class="price__label">on installations</p>
      <p class="price__note">*terms and conditions<br>apply</p>
    </div>
    <div class="price">
      <svg class="price__icon" width="52" height="44" viewBox="0 0 52 44" aria-hidden="true">
        <polygon points="6,8 40,4 44,20 10,24" fill="var(--orange-deep)"/>
        <circle cx="38" cy="14" r="3" fill="var(--white)"/>
        <rect x="14" y="24" width="5" height="10" fill="var(--orange-deep)"/>
        <rect x="4" y="32" width="16" height="5" fill="var(--orange-deep)"/>
      </svg>
      <p class="price__label">CCTV systems starting</p>
      <p class="price__label">from <span class="price__big">£595 + VAT</span></p>
      <p class="price__label">(based on 2 cameras)</p>
    </div>
  </div>

  <p class="always">Kelvor Guard Installations are always there, always available, wherever and whenever you need us.</p>

  <footer class="footer">
    <svg class="footer__bg" width="470" height="42" viewBox="0 0 470 42" aria-hidden="true">
      <rect width="470" height="42" fill="var(--charcoal)"/>
      <polygon points="196,0 470,0 470,42 180,42" fill="var(--orange-deep)"/>
    </svg>
    <div class="footer__phone">
      <svg width="18" height="18" viewBox="0 0 18 18" aria-hidden="true"><circle cx="9" cy="9" r="8" fill="none" stroke="var(--white)" stroke-width="1.5"/><path d="M6 4.5l1.6 2.6-1 1.1c.6 1.4 1.7 2.5 3.1 3.1l1.1-1 2.6 1.6-.6 1.7c-3.6-.2-7.1-3.7-7.3-7.3z" fill="var(--white)"/></svg>
      01632 908417
    </div>
    <div class="footer__contact">
      <p class="footer__web">operations@kelvorguardinstalls.co.uk &nbsp;|&nbsp; www.kelvorguardinstalls.co.uk</p>
      <p class="footer__address">14 Marlow Close, Brentwood, Essex, CM15 9QT</p>
    </div>
  </footer>
</section>

<!-- Side two: services -->
<section class="flyer flyer--info">
  <div class="photo photo--hero" role="img" aria-label="Photograph of a wall-mounted security touch panel beside a modern kitchen"></div>

  <svg class="logo-plate" viewBox="0 0 215 95" aria-hidden="true">
    <polygon points="27,0 215,0 215,95 0,95" fill="var(--white)"/>
    <polygon points="0,0 15,0 39,95 25,95" fill="#cfd1d4"/>
  </svg>
  <div class="logo">
    <span class="logo__mark"></span>
    <span class="logo__name">KELVOR GUARD</span>
    <span class="logo__sub">INSTALLATIONS</span>
  </div>

  <h2 class="safe-banner">Are you looking to keep you and your premises <span class="safe-banner__word">safe?</span></h2>

  <ul class="benefits">
    <li><svg width="10" height="10" viewBox="0 0 10 10" aria-hidden="true"><circle cx="5" cy="5" r="4.3" fill="none" stroke="var(--orange-deep)"/><path d="M2.8 5l1.6 1.6 3-3.2" stroke="var(--orange-deep)" stroke-width="1.3" fill="none"/></svg>Kelvor Guard Installations install, maintain and repair all intruder alarms, CCTV, intercom and access control</li>
    <li><svg width="10" height="10" viewBox="0 0 10 10" aria-hidden="true"><circle cx="5" cy="5" r="4.3" fill="none" stroke="var(--orange-deep)"/><path d="M2.8 5l1.6 1.6 3-3.2" stroke="var(--orange-deep)" stroke-width="1.3" fill="none"/></svg>View, control and manage your security systems anywhere in the world</li>
    <li><svg width="10" height="10" viewBox="0 0 10 10" aria-hidden="true"><circle cx="5" cy="5" r="4.3" fill="none" stroke="var(--orange-deep)"/><path d="M2.8 5l1.6 1.6 3-3.2" stroke="var(--orange-deep)" stroke-width="1.3" fill="none"/></svg>Feel at ease with monitoring services &amp; police response tailored to suit you and your business</li>
    <li><svg width="10" height="10" viewBox="0 0 10 10" aria-hidden="true"><circle cx="5" cy="5" r="4.3" fill="none" stroke="var(--orange-deep)"/><path d="M2.8 5l1.6 1.6 3-3.2" stroke="var(--orange-deep)" stroke-width="1.3" fill="none"/></svg>Kelvor Guard can takeover any existing security system and offer maintenance checks to guarantee the best performance for you and your premises</li>
    <li><svg width="10" height="10" viewBox="0 0 10 10" aria-hidden="true"><circle cx="5" cy="5" r="4.3" fill="none" stroke="var(--orange-deep)"/><path d="M2.8 5l1.6 1.6 3-3.2" stroke="var(--orange-deep)" stroke-width="1.3" fill="none"/></svg>Kelvor Guard understand that being security conscious is ever increasing, protecting your property and family is a number one priority</li>
    <li><svg width="10" height="10" viewBox="0 0 10 10" aria-hidden="true"><circle cx="5" cy="5" r="4.3" fill="none" stroke="var(--orange-deep)"/><path d="M2.8 5l1.6 1.6 3-3.2" stroke="var(--orange-deep)" stroke-width="1.3" fill="none"/></svg>Our fully insured and accredited team offer quality, safety and cost efficiency throughout the whole process</li>
    <li><svg width="10" height="10" viewBox="0 0 10 10" aria-hidden="true"><circle cx="5" cy="5" r="4.3" fill="none" stroke="var(--orange-deep)"/><path d="M2.8 5l1.6 1.6 3-3.2" stroke="var(--orange-deep)" stroke-width="1.3" fill="none"/></svg>Kelvor Guard Installations are using the latest cloud-based technology to stay connected with your home and business 24/7</li>
  </ul>

  <div class="trust">
    <span class="trust__name">Tradevouch</span>
    <span class="badge" aria-label="NQPRB intruder accreditation badge"></span>
    <span class="badge badge--square" aria-label="NQPRB accreditation badge"></span>
    <span class="badge" aria-label="NQPRB CCTV accreditation badge"></span>
  </div>

  <p class="closing">If you are looking to improve the security in your home, office or commercial property<br>then call a member of our team today for a free quote.</p>

  <footer class="footer">
    <svg class="footer__bg" width="470" height="42" viewBox="0 0 470 42" aria-hidden="true">
      <rect width="470" height="42" fill="var(--charcoal)"/>
      <polygon points="196,0 470,0 470,42 180,42" fill="var(--orange-deep)"/>
    </svg>
    <div class="footer__phone">
      <svg width="18" height="18" viewBox="0 0 18 18" aria-hidden="true"><circle cx="9" cy="9" r="8" fill="none" stroke="var(--white)" stroke-width="1.5"/><path d="M6 4.5l1.6 2.6-1 1.1c.6 1.4 1.7 2.5 3.1 3.1l1.1-1 2.6 1.6-.6 1.7c-3.6-.2-7.1-3.7-7.3-7.3z" fill="var(--white)"/></svg>
      01632 908417
    </div>
    <div class="footer__contact">
      <p class="footer__web">operations@kelvorguardinstalls.co.uk &nbsp;|&nbsp; www.kelvorguardinstalls.co.uk</p>
      <p class="footer__address">14 Marlow Close, Brentwood, Essex, CM15 9QT</p>
    </div>
  </footer>
</section>

</body>
</html>
```